Luxury Wine Label for New Startup Winery

We need a wine label for our new winery startup. We have worked with a local designer but do not feel the resulting label / logo have the elevation required to present our brand as a luxury wine. Our winery is called "Quailbrook Vineyards" and we are focused on extremely high quality hand crafted artisan and estate wines from the Pacific Northwest.
We would like to see designs that utilize a tree line, or other imagery that represents the "Quailbrook" part of our company name. Another interesting feature could be wood grain.
A logo will be required based on your design so please design with this in mind:
This logo should be consistent with the wine bottle label design, and should be representative of our high end exclusive wine while giving a sense of place (Oregon/ Pacific Northwest.)
I will supply an image of the design we received from our local designer, PLEASE NOTE: in general we do like wood grain and tree line concepts but feel the execution was poorly done.
ATTN: Logo design should be suitable for use on: Bottles (Red wine/rose/white wine), Bussiness cards, vehicle signage, business signage, etc
P.S.:
If you have a design that is not outside the box we are still interested in seeing it.
Label is for a burgundy style bottle with a label height of 3.5 - 4" and a width of 3.5-4"
any label <= 4"x4" and >=3.5"x3.5" will be acceptable:
HOWEVER Width should be greater than or equal to height due to the bottle format
Target Market(s)
Wine enthusiasts with adequate discretionary budgets to afford $100 bottles of wine.
Industry/Entity Type
Wine / Winery
Requirements
Must have
- A sense of luxury, a feel of exclusivity, and a theme consistent with our product and brand name
Nice to have
- Tree line, wood grain or other wood themes. Serif fonts
Should not have
- anything cheesy, off topic, hard to read script fonts or anything that makes the label hard to read from a few feet away or too busy

```html
<!DOCTYPE html>
<html lang="en">
<head>
<meta charset="utf-8">
<title>Quailbrook Vineyards — Syrah Label</title>
<link rel="stylesheet" href="https://fonts.googleapis.com/css2?family=Tinos:wght@400;700&family=Great+Vibes&display=swap">
<style>
  :root {
    --canvas: #ffffff;
    --label-black: #000000;
    --silver: #c9c9cc;
    --silver-dark: #8d8d92;
    --gold: #c9a24a;
    --gold-dark: #8a6a24;
    --wood-dark: #4a2418;
    --wood-mid: #7a3f2a;
    --wood-light: #9c5a3c;
    --white: #ffffff;
    --name-silver: #bdbdc2;
  }
  * { margin: 0; padding: 0; box-sizing: border-box; }
  html, body { width: 1112px; height: 1200px; overflow: hidden; background: var(--canvas); }
  .canvas { position: relative; width: 1112px; height: 1200px; background: var(--canvas); }

  .label-main {
    position: absolute; left: 135px; top: 153px; width: 844px; height: 685px;
    background: var(--label-black);
  }
  .silver-rule {
    position: absolute; left: 0; width: 100%; height: 7px;
    background: linear-gradient(90deg, var(--silver-dark), var(--silver) 35%, #e8e8ea 55%, var(--silver) 75%, var(--silver-dark));
  }
  .silver-rule.top { top: 23px; }
  .silver-rule.bottom { top: 655px; }

  .landscape {
    position: absolute; left: 194px; top: 114px; width: 456px; height: 240px;
    background: radial-gradient(ellipse at 50% 55%, #6b5424 0%, #3a2c10 45%, rgba(0,0,0,0) 72%);
  }
  .seal {
    position: absolute; left: 334px; top: 207px; width: 172px; height: 172px;
    border-radius: 50%;
    background: radial-gradient(circle at 40% 35%, #d4d4d6, #9a9a9e 60%, #6c6c70);
  }

  .brand-name {
    position: absolute; left: 0; top: 418px; width: 100%;
    text-align: center;
    font-family: "Tinos", "Times New Roman", serif;
    font-weight: 700; font-size: 82px; letter-spacing: 5px; text-indent: 5px;
    color: var(--name-silver); line-height: 1;
  }
  .brand-sub {
    position: absolute; left: 0; top: 518px; width: 100%;
    text-align: center;
    font-family: "Tinos", "Times New Roman", serif;
    font-weight: 400; font-size: 40px; letter-spacing: 22px; text-indent: 22px;
    color: var(--white); line-height: 1;
  }

  .varietal-band {
    position: absolute; left: 135px; top: 866px; width: 844px; height: 183px;
    overflow: hidden;
  }
  .wood {
    position: absolute; inset: 0;
    background:
      radial-gradient(ellipse at 80% 35%, var(--wood-dark) 0%, rgba(74,36,24,0) 30%),
      linear-gradient(175deg, var(--wood-mid), var(--wood-light) 40%, var(--wood-mid) 70%, var(--wood-dark));
  }
  .gold-rule {
    position: absolute; left: 0; width: 100%; height: 4px;
    background: linear-gradient(90deg, var(--gold-dark), var(--gold) 40%, #e6c46e 60%, var(--gold-dark));
  }
  .gold-rule.top { top: 13px; }
  .gold-rule.bottom { top: 171px; }
  .varietal {
    position: absolute; left: 0; top: 36px; width: 100%;
    text-align: center;
    font-family: "Great Vibes", cursive;
    font-size: 100px; line-height: 1; color: var(--white);
  }
</style>
</head>
<body>
<main class="canvas">
  <section class="label-main">
    <div class="silver-rule top"></div>
    <div class="landscape" role="img" aria-label="Gold engraved mountain range with a line of evergreen trees"></div>
    <div class="seal" aria-hidden="true"></div>
    <h1 class="brand-name">QUAILBROOK</h1>
    <p class="brand-sub">VINEYARDS</p>
    <div class="silver-rule bottom"></div>
  </section>

  <section class="varietal-band">
    <div class="wood" role="img" aria-label="Dark walnut wood grain with a swirling knot"></div>
    <div class="gold-rule top"></div>
    <p class="varietal">Syrah</p>
    <div class="gold-rule bottom"></div>
  </section>
</main>
</body>
</html>
```